velorimo.gr wordpress makeover

We need a makeover of our wordpress website velorimo.gr We are a company that provides astrology services via phone either by billable phone number or by prepaid packages.This is what we sell. Moreover, we share everyday astrology related articles to our blog. It will be a multy page website. Our goal is always to sell our phone prepaid packages or to make the visitor of the website call our billable numbers. Our website should have:
-a home page introducing its content (astrologers, call packages, blog section with categories).
-astrologers page (you can see the existing one to understand)
-Phone packages page (eshop page where you can buy prepaid phone packages. woo commerce maybe)
- Blog page divined by categories.
The website should have places for display banners eg. a sidebar.
I will provide some screen shots of websites we like. You can always visit our existing website www.velorimo.gr to see it for yourself.

Target Market(s)

people seeking for future telling - astrologer services via phone. People who like to be informed about everyday astrology predictions

Industry/Entity Type

Astrology - tarot services via phone

Coding

Coded - Design and coding required

Number of Pages Required

5+ page

Font styles to use
Decorative
Script

Colors
6B429C
8869AF
B7A5CE
E3DAEB
F3F0F8

Requirements
Must have
• -Home page -Astrologers page -Phone packages page (eshop) -Blog page with categories - Made following the guidelines of quenbly so as to be efficient in quenbly ads marketing. Mobile friendly.
Nice to have
• Nice call to action buttons to call or buy packages. Sidebar with banner ads of maybe our offers.

```html
<!DOCTYPE html>
<html lang="el">
<head>
<meta charset="utf-8">
<title>velorimo.gr</title>
<link rel="stylesheet" href="https://fonts.googleapis.com/css2?family=Didact+Gothic&family=Noto+Sans:wght@400;500;600&family=Noto+Sans+Symbols+2&family=Lobster&display=swap">
<style>
:root{
  --bg-deep:#12041d;
  --bg-mid:#240a3a;
  --card:#2b0f47;
  --card-line:#4a2a6e;
  --accent:#6a1cff;
  --accent-2:#a236f7;
  --zodiac:#3e1779;
  --zodiac-art:#d9a462;
  --gold:#ffe200;
  --white:#ffffff;
  --muted:#b7a5ce;
  --tab-muted:#a796bd;
}
*{margin:0;padding:0;box-sizing:border-box}
html,body{width:1200px;height:3136px;overflow:hidden}
body{
  font-family:"Noto Sans",sans-serif;color:var(--white);
  background:
    radial-gradient(ellipse 700px 500px at 700px 300px,#3b1254 0%,transparent 70%),
    radial-gradient(ellipse 600px 500px at 100px 1900px,#2c0b44 0%,transparent 70%),
    radial-gradient(ellipse 700px 500px at 1000px 2800px,#3a1046 0%,transparent 70%),
    linear-gradient(180deg,#2a0c3f 0%,var(--bg-deep) 35%,#160522 70%,#22082f 100%);
  position:relative;
}
.abs{position:absolute}
.center-x{left:0;width:1200px;text-align:center}

/* header */
.logo{display:flex;align-items:center;gap:6px;font-size:46px;color:var(--white);font-weight:400;letter-spacing:.5px}
.logo-dot{width:30px;height:30px;border-radius:50%;background:#6b5a86}
.site-logo{left:52px;top:36px}
.main-nav{left:397px;top:52px;display:flex;gap:44px;font-size:16px}
.main-nav a{color:var(--white);text-decoration:none}
.search-btn{left:928px;top:44px;width:38px;height:38px;border:2px solid #8b63d9;border-radius:50%;display:flex;align-items:center;justify-content:center}
.call-pill{left:985px;top:40px;width:152px;height:46px;border:2px solid var(--white);border-radius:23px;background:var(--accent);display:flex;align-items:center;justify-content:center;gap:4px;font-family:"Lobster",sans-serif;font-size:36px;color:var(--white)}

/* hero */
.hero-title{top:222px;font-family:"Didact Gothic",sans-serif;font-size:42px;letter-spacing:1px}
.hero-sub{top:296px;font-size:21px;line-height:28px;color:#eee}

/* articles */
.article-grid{left:102px;top:405px;width:996px;display:grid;grid-template-columns:repeat(3,322px);gap:15px 15px}
.article-card{height:122px;background:rgba(43,15,71,.75);border:1px solid var(--card-line);display:flex;align-items:center;padding:0 13px;gap:14px}
.article-img{width:101px;height:90px;flex:none}
.article-card h3{font-weight:400;font-size:20px;margin-bottom:6px}
.article-card p{font-size:12px;line-height:14px;color:#ddd}

.btn{display:flex;align-items:center;justify-content:center;width:158px;height:49px;border:2px solid var(--white);border-radius:25px;background:linear-gradient(90deg,var(--accent),var(--accent-2));font-size:15px;color:var(--white);letter-spacing:.3px;left:521px}

/* tabs */
.tabs{left:101px;top:860px;display:flex;gap:56px;font-family:"Didact Gothic",sans-serif;font-size:23px;font-weight:600;color:var(--tab-muted);letter-spacing:1px}
.tabs .active{color:#8c4cff}
.tab-line{left:96px;top:912px;width:999px;height:2px;background:#6a2fd8}
.tab-notch{left:150px;top:906px;width:0;height:0;border-left:6px solid transparent;border-right:6px solid transparent;border-bottom:6px solid #6a2fd8}
.zodiac-row{left:98px;top:950px;display:flex;gap:9px}
.zodiac-sign{position:relative;width:160px;height:160px;border-radius:50%;background:var(--zodiac);overflow:hidden}
.zodiac-glyph{position:absolute;left:0;top:10px;width:160px;text-align:center;font-family:"Noto Sans Symbols 2","Noto Sans Symbols",sans-serif;font-size:30px;line-height:34px;color:var(--white)}
.zodiac-art{position:absolute;left:20px;top:48px;width:120px;height:108px;border-radius:50% 50% 45% 45%;background:radial-gradient(ellipse at 50% 45%,var(--zodiac-art) 0%,#c48f52 45%,rgba(196,143,82,0) 72%)}
.carousel-arrows{left:1132px;top:1000px;display:flex;flex-direction:column;gap:10px}

/* astrologers */
.section-title{font-family:"Didact Gothic",sans-serif;font-size:50px;letter-spacing:1.5px}
.astro-row{left:98px;top:1370px;display:flex;gap:22px}
.astro-card{width:234px;height:382px;border:2px solid var(--white);border-radius:117px;overflow:hidden;background:#1a0630;text-align:center}
.astro-photo{height:150px}
.astro-card h4{font-weight:400;font-size:16px;margin-top:26px}
.astro-role{font-size:12px;color:var(--gold);margin-top:2px}
.astro-bio{font-size:11px;line-height:15px;color:#eee;padding:0 18px;margin-top:20px}
.astro-call{display:flex;align-items:center;justify-content:center;gap:4px;font-family:"Lobster",sans-serif;font-size:32px;color:var(--gold);margin-top:16px}

/* packages */
.package-row{left:97px;top:2119px;display:flex;gap:23px}
.package{width:320px;height:236px;background:var(--card);border-radius:4px;text-align:center;padding-top:38px}
.package.featured{background:linear-gradient(180deg,var(--accent),#8f30f4)}
.package-price{font-family:"Lobster",sans-serif;font-size:50px;color:var(--gold);line-height:50px}
.package-time{font-size:17px;color:var(--gold);margin-top:2px}
.package p{font-size:12px;line-height:14px;color:#eee;padding:0 40px;margin-top:42px}

/* newsletter + footer */
.rule{left:0;width:1200px;height:1px;background:#3e2558}
.newsletter-title{top:2604px;font-family:"Lobster",sans-serif;font-size:34px}
.newsletter-form{left:271px;top:2675px;display:flex;gap:11px}
.field{width:239px;height:50px;border:2px solid var(--white);border-radius:25px;padding-left:15px;display:flex;align-items:center;font-size:15px;color:#ccc}
.join-btn{width:158px;height:50px;border:2px solid var(--white);border-radius:25px;background:linear-gradient(90deg,var(--accent),var(--accent-2));display:flex;align-items:center;justify-content:center;font-size:15px}
.footer-logo{left:0;width:1200px;top:2818px;justify-content:center}
.footer-links{left:0;width:1200px;display:flex;justify-content:center;font-size:12px;letter-spacing:.3px}
.signs-nav{top:2911px;gap:0}
.signs-nav span{padding:0 18px}
.info-nav{top:2992px;gap:44px}
.copyright{top:3046px;font-size:12px}
.social{left:1119px;width:42px;height:42px;border-radius:50%}
</style>
</head>
<body>

<header>
  <div class="abs site-logo logo">velorimo<span class="logo-dot"></span></div>
  <nav class="abs main-nav"><a href="#">Blog</a><a href="#">Μέντιουμ Αστρολόγοι</a><a href="#">Αγορά Χρόνου Ομιλίας</a></nav>
  <div class="abs search-btn"><svg width="12" height="12" viewBox="0 0 12 12"><circle cx="5" cy="5" r="3.5" fill="none" stroke="#fff" stroke-width="1.6"/><path d="M7.6 7.6L11 11" stroke="#fff" stroke-width="1.8"/></svg></div>
  <div class="abs call-pill"><svg width="26" height="26" viewBox="0 0 24 24"><path fill="#fff" d="M6.6 10.8a15.1 15.1 0 006.6 6.6l2.2-2.2c.3-.3.7-.4 1-.2 1.1.4 2.3.6 3.6.6.6 0 1 .4 1 1V20c0 .6-.4 1-1 1A17 17 0 013 4c0-.6.4-1 1-1h3.5c.6 0 1 .4 1 1 0 1.3.2 2.5.6 3.6.1.3 0 .7-.2 1z"/></svg>14872</div>
</header>

<section class="hero">
  <h1 class="abs center-x hero-title">WELCOME TO VELORIMO.GR</h1>
  <p class="abs center-x hero-sub">Lorem ipsum dolor sit amet, consectetur adipiscing elit<br>ed do eiusmod tempor incididunt ut labore et</p>
</section>

<section class="abs article-grid">
  <article class="article-card"><div class="article-img" role="img" aria-label="Birdcage with a star above an open hand" style="background:linear-gradient(160deg,#4fa3d6,#e0a53a)"></div><div><h3>Latest Articles</h3><p>Lorem ipsum dolor sit amet,<br>consectetur adipiscinlore</p></div></article>
  <article class="article-card"><div class="article-img" role="img" aria-label="Tarot cards and candles on a table" style="background:linear-gradient(160deg,#3a2a22,#8a6a4a)"></div><div><h3>Latest Articles</h3><p>Lorem ipsum dolor sit amet,<br>consectetur adipiscinlore</p></div></article>
  <article class="article-card"><div class="article-img" role="img" aria-label="Crescent moon in a glowing blue sky" style="background:linear-gradient(160deg,#0a5fa8,#3ad0f0)"></div><div><h3>Latest Articles</h3><p>Lorem ipsum dolor sit amet,<br>consectetur adipiscinlore</p></div></article>
  <article class="article-card"><div class="article-img" role="img" aria-label="Blue zodiac wheel" style="background:radial-gradient(circle,#9fb8ff,#233a9a)"></div><div><h3>Latest Articles</h3><p>Lorem ipsum dolor sit amet,<br>consectetur adipiscinlore</p></div></article>
  <article class="article-card"><div class="article-img" role="img" aria-label="Cyclist carried by colourful balloons" style="background:linear-gradient(160deg,#4f9fd0,#c7c46a)"></div><div><h3>Latest Articles</h3><p>Lorem ipsum dolor sit amet,<br>consectetur adipiscinlore</p></div></article>
  <article class="article-card"><div class="article-img" role="img" aria-label="Hands reading tarot cards" style="background:linear-gradient(160deg,#8a1e10,#2a1208)"></div><div><h3>Latest Articles</h3><p>Lorem ipsum dolor sit amet,<br>consectetur adipiscinlore</p></div></article>
</section>
<a class="abs btn" style="top:714px">MORE ARTICLES</a>

<section>
  <div class="abs tabs"><span class="active">Astrology</span><span>Horoscope</span><span>Panchang</span><span>Zodiac</span></div>
  <div class="abs tab-line"></div><div class="abs tab-notch"></div>
  <div class="abs zodiac-row">
    <div class="zodiac-sign"><span class="zodiac-glyph">&#x2648;&#xFE0E;</span><div class="zodiac-art" role="img" aria-label="Aries: golden ram head illustration"></div></div>
    <div class="zodiac-sign"><span class="zodiac-glyph">&#x2649;&#xFE0E;</span><div class="zodiac-art" role="img" aria-label="Taurus: golden bull head illustration"></div></div>
    <div class="zodiac-sign"><span class="zodiac-glyph">&#x264A;&#xFE0E;</span><div class="zodiac-art" role="img" aria-label="Gemini: golden twins illustration"></div></div>
    <div class="zodiac-sign"><span class="zodiac-glyph">&#x264B;&#xFE0E;</span><div class="zodiac-art" role="img" aria-label="Cancer: golden crab illustration"></div></div>
    <div class="zodiac-sign"><span class="zodiac-glyph">&#x264C;&#xFE0E;</span><div class="zodiac-art" role="img" aria-label="Leo: golden lion head illustration"></div></div>
    <div class="zodiac-sign"><span class="zodiac-glyph">&#x264D;&#xFE0E;</span><div class="zodiac-art" role="img" aria-label="Virgo: golden maiden illustration"></div></div>
  </div>
  <div class="abs carousel-arrows">
    <svg width="16" height="16" viewBox="0 0 16 16"><path d="M11 2L5 8l6 6" fill="none" stroke="#fff" stroke-width="2.5"/></svg>
    <svg width="16" height="16" viewBox="0 0 16 16"><path d="M5 2l6 6-6 6" fill="none" stroke="#fff" stroke-width="2.5"/></svg>
  </div>
</section>

<section>
  <h2 class="abs center-x section-title" style="top:1250px">Μέντιουμ Αστρολόγοι</h2>
  <div class="abs astro-row">
    <article class="astro-card"><div class="astro-photo" role="img" aria-label="Portrait of an astrologer against a starry sky" style="background:linear-gradient(180deg,#2a2a8a,#5a2a9a)"></div><h4>Αλέξανδρος</h4><div class="astro-role">(Αστρολόγος, Μέντιουμ)</div><p class="astro-bio">Αν θέλεις μια αληθινή πρόβλεψη κάλεσε με ΤΩΡΑ. Η αστρολογία θα με κατευθύνει και θα δώσω λύσεις στα πρόβλημα και</p><div class="astro-call"><svg width="22" height="22" viewBox="0 0 24 24"><path fill="#ffe200" d="M6.6 10.8a15.1 15.1 0 006.6 6.6l2.2-2.2c.3-.3.7-.4 1-.2 1.1.4 2.3.6 3.6.6.6 0 1 .4 1 1V20c0 .6-.4 1-1 1A17 17 0 013 4c0-.6.4-1 1-1h3.5c.6 0 1 .4 1 1 0 1.3.2 2.5.6 3.6.1.3 0 .7-.2 1z"/></svg>14872</div></article>
    <article class="astro-card"><div class="astro-photo" role="img" aria-label="Portrait of an astrologer on a violet background" style="background:linear-gradient(180deg,#7a5aa8,#5a2a8a)"></div><h4>Αλέξανδρος</h4><div class="astro-role">(Αστρολόγος, Μέντιουμ)</div><p class="astro-bio">Αν θέλεις μια αληθινή πρόβλεψη κάλεσε με ΤΩΡΑ. Η αστρολογία θα με κατευθύνει και θα δώσω λύσεις στα πρόβλημα και</p><div class="astro-call"><svg width="22" height="22" viewBox="0 0 24 24"><path fill="#ffe200" d="M6.6 10.8a15.1 15.1 0 006.6 6.6l2.2-2.2c.3-.3.7-.4 1-.2 1.1.4 2.3.6 3.6.6.6 0 1 .4 1 1V20c0 .6-.4 1-1 1A17 17 0 013 4c0-.6.4-1 1-1h3.5c.6 0 1 .4 1 1 0 1.3.2 2.5.6 3.6.1.3 0 .7-.2 1z"/></svg>14872</div></article>
    <article class="astro-card"><div class="astro-photo" role="img" aria-label="Portrait of an astrologer before a golden zodiac wheel" style="background:linear-gradient(180deg,#c07a3a,#f0a040)"></div><h4>Αλέξανδρος</h4><div class="astro-role">(Αστρολόγος, Μέντιουμ)</div><p class="astro-bio">Αν θέλεις μια αληθινή πρόβλεψη κάλεσε με ΤΩΡΑ. Η αστρολογία θα με κατευθύνει και θα δώσω λύσεις στα πρόβλημα και</p><div class="astro-call"><svg width="22" height="22" viewBox="0 0 24 24"><path fill="#ffe200" d="M6.6 10.8a15.1 15.1 0 006.6 6.6l2.2-2.2c.3-.3.7-.4 1-.2 1.1.4 2.3.6 3.6.6.6 0 1 .4 1 1V20c0 .6-.4 1-1 1A17 17 0 013 4c0-.6.4-1 1-1h3.5c.6 0 1 .4 1 1 0 1.3.2 2.5.6 3.6.1.3 0 .7-.2 1z"/></svg>14872</div></article>
    <article class="astro-card"><div class="astro-photo" role="img" aria-label="Portrait of an astrologer before a pink zodiac ring" style="background:linear-gradient(180deg,#8a1a6a,#5a1a8a)"></div><h4>Αλέξανδρος</h4><div class="astro-role">(Αστρολόγος, Μέντιουμ)</div><p class="astro-bio">Αν θέλεις μια αληθινή πρόβλεψη κάλεσε με ΤΩΡΑ. Η αστρολογία θα με κατευθύνει και θα δώσω λύσεις στα πρόβλημα και</p><div class="astro-call"><svg width="22" height="22" viewBox="0 0 24 24"><path fill="#ffe200" d="M6.6 10.8a15.1 15.1 0 006.6 6.6l2.2-2.2c.3-.3.7-.4 1-.2 1.1.4 2.3.6 3.6.6.6 0 1 .4 1 1V20c0 .6-.4 1-1 1A17 17 0 013 4c0-.6.4-1 1-1h3.5c.6 0 1 .4 1 1 0 1.3.2 2.5.6 3.6.1.3 0 .7-.2 1z"/></svg>14872</div></article>
  </div>
  <a class="abs btn" style="top:1789px">VIEW MORE</a>
</section>

<section>
  <h2 class="abs center-x section-title" style="top:2013px">Αγορά Χρόνου Ομιλίας</h2>
  <div class="abs package-row">
    <div class="package"><div class="package-price">30€</div><div class="package-time">20 mins of talking time.</div><p>Lorem ipsum dolor sit amet, consectetur adipiscing elit, sed do eiusmod tempor incididunt ut labore et dolo aliqua.</p></div>
    <div class="package featured"><div class="package-price">40€</div><div class="package-time">30 mins of talking time.</div><p>Lorem ipsum dolor sit amet, consectetur adipiscing elit, sed do eiusmod tempor incididunt ut labore et dolo aliqua.</p></div>
    <div class="package"><div class="package-price">50€</div><div class="package-time">40 mins of talking time.</div><p>Lorem ipsum dolor sit amet, consectetur adipiscing elit, sed do eiusmod tempor incididunt ut labore et dolo aliqua.</p></div>
  </div>
  <a class="abs btn" style="top:2395px">EXPLORE MORE</a>
</section>

<div class="abs rule" style="top:2573px"></div>
<section>
  <h2 class="abs center-x newsletter-title">Join Our Daily Overview Newsletter!</h2>
  <div class="abs newsletter-form"><div class="field">Name:</div><div class="field">Email:</div><div class="join-btn">JOIN NOW</div></div>
</section>
<div class="abs rule" style="top:2786px"></div>

<footer>
  <div class="abs footer-logo logo">velorimo<span class="logo-dot"></span></div>
  <nav class="abs footer-links signs-nav"><span>ARIES</span><span>TAURUS</span><span>GEMINI</span><span>CANCER</span><span>LEO</span><span>VIRGO</span><span>LIBRA</span><span>SCORPIO</span><span>SAGITTARIUS</span><span>CAPRICORN</span><span>AQUARIUS</span><span>PISCES</span></nav>
  <div class="abs rule" style="top:2960px"></div>
  <nav class="abs footer-links info-nav"><span>ABOUT US</span><span>CONTACT US</span><span>ADVERTISING</span><span>SYNDICATION</span><span>PRIVACY</span><span>TERMS</span><span>DO NOT SELL MY INFO</span></nav>
  <p class="abs center-x copyright">© COPYRIGHT • 2022 • VELORIMO.GR</p>
  <div class="abs social" style="top:2946px;background:#2aa3e6" role="img" aria-label="Social link"></div>
  <div class="abs social" style="top:3002px;background:#3b5ea8" role="img" aria-label="Social link"></div>
  <div class="abs social" style="top:3056px;background:#e0306e" role="img" aria-label="Social link"></div>
</footer>

</body>
</html>
```